Ductless Mini Split Business Website

Copper Fern Services is looking to design an eye catching educational website about installing Ductless mini splits.

Similar to this company.
https://www.halvikstream.com/

Coding

Coded - Design and coding required

```html
<!DOCTYPE html>
<html lang="en">
<head>
<meta charset="utf-8">
<title>Copper Fern Services – Ductless Experts</title>
<link href="https://fonts.googleapis.com/css2?family=Montserrat:wght@400;500;600;700&family=Nunito:wght@300;400;600&family=Comfortaa:wght@400;700&display=swap" rel="stylesheet">
<style>
:root{
  --yellow:#ffd400;
  --amber:#f5b72c;
  --ink:#1e1e1e;
  --body:#7a7a7a;
  --line:#e3e3e3;
  --dark:#4b4b4d;
  --light:#f4f4f4;
  --white:#ffffff;
}
*{box-sizing:border-box;margin:0;padding:0}
html,body{width:1200px;height:3480px;overflow:hidden;background:var(--white)}
body{font-family:"Nunito",sans-serif;color:var(--ink)}
.page{position:relative;width:1200px;height:3480px;overflow:hidden}
.abs{position:absolute}
.head{font-family:"Montserrat",sans-serif}
.btn{position:absolute;display:flex;align-items:center;justify-content:center;background:var(--amber);color:var(--ink);font-family:"Montserrat",sans-serif;font-size:16px;border-radius:6px;box-shadow:0 2px 6px rgba(0,0,0,.15)}

/* header */
.topbar{left:0;top:0;width:1200px;height:103px}
.brand{left:118px;top:18px;font-family:"Montserrat",sans-serif;font-weight:700;font-size:24px;color:var(--ink);display:flex;align-items:center;gap:10px}
.brand i{display:block;width:22px;height:22px;border-radius:50%;background:var(--amber)}
.tagline{left:119px;top:70px;font-family:"Montserrat",sans-serif;font-weight:700;font-size:17px;letter-spacing:.5px}
.call{left:672px;top:24px;font-family:"Montserrat",sans-serif;font-size:16px}
.call b{font-weight:700;font-size:18px}
.login{left:976px;top:8px;width:112px;height:52px;background:var(--white);border-radius:6px;display:flex;align-items:center;justify-content:center;font-family:"Montserrat",sans-serif;font-size:16px;box-shadow:0 2px 6px rgba(0,0,0,.15)}
.nav{left:581px;top:76px;display:flex;gap:21px;font-family:"Montserrat",sans-serif;font-size:16px}
.nav .on{border-bottom:2px solid var(--ink);padding-bottom:2px}

/* hero */
.hero{left:0;top:103px;width:1200px;height:657px;background:linear-gradient(180deg,#d9d9d7 0%,#c7c7c3 45%,#6e6f70 75%,#8a8b88 100%)}
.hero-title{left:0;top:276px;width:1130px;text-align:center;font-family:"Montserrat",sans-serif;font-weight:700;font-size:46px;color:var(--white);text-shadow:2px 2px 3px rgba(0,0,0,.4)}
.hero-sub{left:0;top:338px;width:1130px;text-align:center;font-weight:300;font-size:16px;line-height:27px;color:var(--white);text-shadow:1px 1px 2px rgba(0,0,0,.5)}
.dots{left:565px;top:649px;display:flex;gap:11px}
.dots span{width:9px;height:9px;border-radius:50%;background:var(--white)}
.dots .on{background:var(--amber)}

/* about */
.h2{font-family:"Montserrat",sans-serif;font-weight:600;font-size:31px;color:var(--ink)}
.about-text{left:111px;top:886px;width:449px;font-size:16px;font-weight:300;line-height:34.4px;color:var(--body);text-align:justify}
.video{left:653px;top:828px;width:435px;height:304px;background:linear-gradient(135deg,#8a6b5a,#c4b2a0 40%,#5d6b7d 70%,#a34141);box-shadow:0 0 0 2px #eee}
.play{left:841px;top:955px;width:58px;height:58px;border-radius:50%;background:var(--white)}

/* help */
.card-img{position:absolute;top:1374px;width:240px;height:253px}
.card-lbl{position:absolute;top:1627px;width:240px;height:66px;background:var(--white);display:flex;align-items:center;justify-content:center;text-align:center;font-family:"Montserrat",sans-serif;font-size:15.5px;line-height:26px;box-shadow:0 2px 4px rgba(0,0,0,.08)}
.card-lbl.on{background:var(--amber)}
.overlay-txt{position:absolute;left:358px;top:1450px;width:240px;text-align:center;color:var(--white);font-size:16px;font-weight:300;line-height:26px}
.overlay-txt u{display:block;margin-top:6px;font-family:"Montserrat",sans-serif;font-weight:500}
.arrow{position:absolute;top:1486px;width:40px;height:40px;border-radius:50%;background:var(--white);border:1px solid #bbb}

/* why */
.why{position:absolute;top:1959px;width:313px;height:186px;background:var(--white);border:1px solid var(--line);box-shadow:0 2px 6px rgba(0,0,0,.06);text-align:center}
.why h3{margin-top:68px;font-family:"Montserrat",sans-serif;font-weight:500;font-size:16px}
.why p{margin-top:8px;font-size:16px;font-weight:300;line-height:26px;color:var(--body);padding:0 30px}
.ico{position:absolute;top:1918px;width:98px;height:98px;border-radius:50%;background:var(--white);border:1px solid var(--line);display:flex;align-items:center;justify-content:center}
.ico.on{background:var(--amber);border-color:var(--amber)}

/* testimonials */
.avatar{position:absolute;width:86px;height:86px;border-radius:50%;border:3px solid var(--white)}
.t-name{left:223px;top:2378px;font-family:"Montserrat",sans-serif;font-size:16px;color:var(--white)}
.t-text{left:226px;top:2414px;width:310px;font-size:16px;font-weight:300;line-height:26px;color:var(--white);text-align:justify}
.stars{left:226px;top:2536px;color:var(--amber);font-size:18px;letter-spacing:8px}
.form{left:559px;top:2237px;width:526px;height:487px;background:var(--white);border-radius:6px;box-shadow:0 4px 14px rgba(0,0,0,.15)}
.field{position:absolute;height:50px;border:1px solid #d7d7d7;border-radius:6px;font-size:14px;color:#777;padding:0 15px;display:flex;align-items:center;justify-content:space-between}
.field.area{align-items:flex-start;padding-top:14px}
.note{left:835px;top:2630px;width:220px;font-size:12.5px;color:#777;line-height:17px}

/* stats */
.stat{position:absolute;top:2846px;width:330px;text-align:center}
.stat b{display:block;font-family:"Comfortaa",sans-serif;font-weight:700;font-size:54px;color:var(--amber);line-height:60px}
.stat i{display:block;width:96px;height:3px;background:var(--amber);margin:10px auto 18px}
.stat strong{display:block;font-family:"Montserrat",sans-serif;font-weight:500;font-size:15px}
.stat span{display:block;margin-top:6px;font-family:"Montserrat",sans-serif;font-size:15px;color:#444}

/* footer */
.footer{left:0;top:3152px;width:1200px;height:328px;background:linear-gradient(180deg,#575759,#414143)}
.coupon{left:143px;top:3083px;width:942px;height:142px;background:var(--amber);border-radius:4px}
.coupon-inner{position:absolute;left:17px;top:15px;right:17px;bottom:15px;border:2px dashed var(--white)}
.off{left:199px;top:3118px;font-family:"Comfortaa",sans-serif;font-weight:700;font-size:54px}
.c-div{left:480px;top:3119px;width:1px;height:70px;background:rgba(255,255,255,.7)}
.c-text{left:527px;top:3122px;font-family:"Comfortaa",sans-serif;font-size:21px;line-height:34px}
.print{left:865px;top:3129px;width:187px;height:50px;background:var(--white);border-radius:6px;display:flex;align-items:center;justify-content:center;font-family:"Montserrat",sans-serif;font-size:16px}
.fnav{left:0;top:3276px;width:1160px;display:flex;justify-content:center;gap:33px;font-family:"Montserrat",sans-serif;font-size:16px;color:var(--white)}
.social{left:512px;top:3338px;display:flex;gap:13px}
.social span{width:36px;height:36px;border-radius:50%;border:2px solid var(--white)}
.copy{left:0;top:3408px;width:1160px;text-align:center;font-size:16px;color:var(--white)}
</style>
</head>
<body>
<div class="page">

  <!-- header -->
  <div class="abs topbar">
    <svg width="1200" height="103" viewBox="0 0 1200 103"><polygon points="515,0 1200,0 1200,103 451,103" fill="#ffd400"/><polyline points="515,0 451,103" stroke="#1e1e1e" stroke-width="3" fill="none"/></svg>
  </div>
  <div class="abs brand"><i></i>Copper Fern Services</div>
  <div class="abs tagline">DUCTLESS EXPERTS</div>
  <div class="abs call">CALL US TODAY - <b>555-014-2290</b></div>
  <div class="abs login">LOG IN</div>
  <nav class="abs nav"><span class="on">HOME</span><span>ABOUT</span><span>SERVICES</span><span>FINANCE</span><span>REVIEWS</span><span>CONTACT</span></nav>

  <!-- hero -->
  <div class="abs hero" role="img" aria-label="Photo of a couple relaxing on a sofa under a wall-mounted ductless air conditioner"></div>
  <svg class="abs" style="left:0;top:655px" width="1200" height="110" viewBox="0 0 1200 110"><polygon points="1200,3 1200,110 0,110 0,106" fill="#fff"/></svg>
  <div class="abs hero-title">COPPER FERN SERVICES</div>
  <div class="abs hero-sub">Nemo enim ipsam voluptatem quia voluptas sit aspernatur<br>aut odit aut fugit, sed quia consequuntur</div>
  <div class="btn" style="left:484px;top:405px;width:162px;height:52px">GET STARTED</div>
  <div class="abs dots"><span></span><span></span><span class="on"></span><span></span></div>

  <!-- about -->
  <div class="abs h2" style="left:111px;top:832px">ABOUT US</div>
  <p class="abs about-text">Nemo enim ipsam voluptatem quia voluptas sit aspernatur aut odit aut fugit, sed quia consequuntur magni dolores eos qui ratione voluptatem sequi nesciunt. Neque porro quisquam est, qui dolorem ipsum quia dolor sit amet, consectetur, adipisci velit, sed quia non numquam</p>
  <div class="btn" style="left:111px;top:1077px;width:145px;height:50px">READ MORE</div>
  <div class="abs video" role="img" aria-label="Video thumbnail of the service team standing together"></div>
  <div class="abs play"><svg width="58" height="58" viewBox="0 0 58 58"><polygon points="23,18 40,29 23,40" fill="#e21b1b"/></svg></div>

  <!-- help -->
  <svg class="abs" style="left:0;top:1200px" width="1200" height="612" viewBox="0 0 1200 612">
    <polygon points="0,0 1200,0 1200,612 0,612" fill="#f3f3f3"/>
    <polygon points="700,0 1200,0 1200,140" fill="#fdf1d4"/>
    <polygon points="0,500 600,560 1200,520 1200,612 0,612" fill="#f6eed8"/>
  </svg>
  <div class="abs h2" style="left:0;top:1312px;width:1180px;text-align:center">HOW CAN WE HELP YOU</div>
  <div class="card-img" style="left:111px;background:linear-gradient(135deg,#b6b2a5,#6f7d8a)" role="img" aria-label="Technician checking refrigerant gauges"></div>
  <div class="card-img" style="left:358px;background:linear-gradient(135deg,#3e3c3a,#6a6460)" role="img" aria-label="Additions and remodels photo"></div>
  <div class="card-img" style="left:603px;background:linear-gradient(135deg,#c9c3b7,#e3e3e3 50%,#7d8ca0)" role="img" aria-label="Technician installing an outdoor condenser unit"></div>
  <div class="card-img" style="left:848px;background:linear-gradient(135deg,#d9d5cf,#7f8fb4)" role="img" aria-label="Technician servicing an indoor mini split unit"></div>
  <div class="overlay-txt">Nemo enim ipsam voluptatem quia voluptas sit aspernatur aut odit aut fugit, sed quia consequuntur<u>READ MORE</u></div>
  <div class="card-lbl" style="left:111px">BASEBOARD HEAT<br>REPLACEMENT</div>
  <div class="card-lbl on" style="left:358px">ADDITIONS &amp; REMODELS</div>
  <div class="card-lbl" style="left:603px">INSTALLATION</div>
  <div class="card-lbl" style="left:848px">MAINTENANCE</div>
  <div class="arrow" style="left:50px"><svg width="40" height="40" viewBox="0 0 40 40"><polyline points="23,12 15,20 23,28" fill="none" stroke="#333" stroke-width="1.6"/></svg></div>
  <div class="arrow" style="left:1100px"><svg width="40" height="40" viewBox="0 0 40 40"><polyline points="17,12 25,20 17,28" fill="none" stroke="#333" stroke-width="1.6"/></svg></div>

  <!-- why -->
  <div class="abs h2" style="left:0;top:1853px;width:1200px;text-align:center">WHY CHOOSE COPPER FERN</div>
  <div class="why" style="left:111px"><h3>0% FINANCING FOR 60 MONTHS</h3><p>Nemo enim ipsam voluptatem quia voluptas sit aspernatur aut odit aut fugit</p></div>
  <div class="why" style="left:443px"><h3>365 DAY, MONEY BACK GUARANTEE</h3><p>Nemo enim ipsam voluptatem quia voluptas sit aspernatur aut odit aut fugit</p></div>
  <div class="why" style="left:774px"><h3>EXPERTS IN DUCTLESS SERVICES</h3><p>Nemo enim ipsam voluptatem quia voluptas sit aspernatur aut odit aut fugit</p></div>
  <div class="ico" style="left:218px"><svg width="52" height="52" viewBox="0 0 52 52" fill="none" stroke="#f5b72c" stroke-width="2"><rect x="10" y="6" width="28" height="40" rx="2"/><line x1="16" y1="16" x2="32" y2="16"/><line x1="16" y1="23" x2="32" y2="23"/><line x1="16" y1="30" x2="26" y2="30"/><line x1="44" y1="14" x2="30" y2="40"/></svg></div>
  <div class="ico on" style="left:550px"><svg width="52" height="52" viewBox="0 0 52 52" fill="none" stroke="#1e1e1e" stroke-width="2"><circle cx="28" cy="32" r="14"/><path d="M22 16 L34 16 L30 10 L26 10 Z"/><text x="23" y="38" font-family="Montserrat" font-size="16" fill="#1e1e1e" stroke="none">$</text></svg></div>
  <div class="ico" style="left:882px"><svg width="52" height="52" viewBox="0 0 52 52" fill="none" stroke="#f5b72c" stroke-width="2"><path d="M12 24 A14 14 0 0 1 40 24 Z"/><line x1="8" y1="26" x2="44" y2="26"/><rect x="22" y="6" width="8" height="8"/><path d="M10 46 L10 40 Q26 32 42 40 L42 46"/></svg></div>
  <div class="abs" style="left:707px;top:2104px;width:48px;height:41px;background:var(--amber)"><svg width="48" height="41" viewBox="0 0 48 41"><line x1="17" y1="20" x2="31" y2="20" stroke="#1e1e1e" stroke-width="2"/><polyline points="26,15 31,20 26,25" fill="none" stroke="#1e1e1e" stroke-width="2"/></svg></div>

  <!-- testimonials -->
  <svg class="abs" style="left:0;top:2232px" width="1200" height="560" viewBox="0 0 1200 560">
    <defs><linearGradient id="tg" x1="0" y1="0" x2="0" y2="1"><stop offset="0" stop-color="#5a5a5c"/><stop offset="1" stop-color="#3c3c3e"/></linearGradient></defs>
    <polygon points="0,0 600,0 600,470 0,470" fill="url(#tg)"/>
    <polygon points="600,100 1200,80 1200,555 600,500" fill="url(#tg)"/>
  </svg>
  <div class="abs" style="left:100px;top:2530px;width:460px;height:170px;background:linear-gradient(180deg,rgba(90,90,92,0),#707072)" role="img" aria-label="Photo of a family relaxing on a couch"></div>
  <div class="abs head" style="left:111px;top:2298px;font-weight:600;font-size:31px;color:var(--white)">TESTIMONIALS</div>
  <div class="avatar" style="left:111px;top:2358px;background:#8aa1b8" role="img" aria-label="Customer portrait"></div>
  <div class="avatar" style="left:117px;top:2453px;width:72px;height:72px;border:none;background:#9aa7b3" role="img" aria-label="Customer portrait"></div>
  <div class="avatar" style="left:117px;top:2552px;width:72px;height:72px;border:none;background:#7d7269" role="img" aria-label="Customer portrait"></div>
  <div class="abs t-name">JHON DOE</div>
  <p class="abs t-text">Nemo enim ipsam voluptatem quia voluptas sit aspernatur aut odit aut fugit, sed quia consequuntur magni dolores eos qui ratione voluptatem sequi nesciunt</p>
  <div class="abs stars">★★★★★</div>

  <div class="abs form">
    <div class="field" style="left:35px;top:54px;width:217px">Name</div>
    <div class="field" style="left:276px;top:54px;width:215px">Email</div>
    <div class="field" style="left:35px;top:114px;width:217px">Phone No</div>
    <div class="field" style="left:276px;top:114px;width:215px">Select Service <span>▾</span></div>
    <div class="field" style="left:35px;top:179px;width:217px">Zip Code</div>
    <div class="field" style="left:276px;top:179px;width:215px">Are You A New Customer <span>▾</span></div>
    <div class="field area" style="left:35px;top:245px;width:456px;height:125px">Write Your Message Here...</div>
    <div class="btn" style="left:35px;top:385px;width:217px;height:49px;font-size:16px">SEND</div>
  </div>
  <div class="abs note">Our Customer SupportTeam Will Contact You With In 24 Hrs.</div>

  <!-- stats -->
  <div class="stat" style="left:94px"><b>3000</b><i></i><strong>CUSTOMERS</strong><span>100% Satisfied With Our Work</span></div>
  <div class="stat" style="left:436px"><b>1500</b><i></i><strong>PROFESSIONAL</strong><span>Engineers Working In Our Company</span></div>
  <div class="stat" style="left:779px"><b>30</b><i></i><strong>BRANCHES</strong><span>Operating &amp; It's Sorrounding</span></div>

  <!-- footer -->
  <div class="abs footer" role="img" aria-label="Faded background photo of a living room"></div>
  <div class="abs coupon"><div class="coupon-inner"></div></div>
  <div class="abs off">20 % OFF</div>
  <div class="abs c-div"></div>
  <div class="abs c-text">AC or Heating Maintenance<br>&amp; Repair</div>
  <div class="abs print">PRINT YOUR COUPON</div>
  <nav class="abs fnav"><span>HOME</span><span>ABOUT</span><span>SERVICES</span><span>FINANCE</span><span>REVIEWS</span><span>CONTACT</span></nav>
  <div class="abs social"><span aria-label="Social link"></span><span aria-label="Social link"></span><span aria-label="Social link"></span><span aria-label="Social link"></span></div>
  <div class="abs copy">© 2019. All rights reserved. Privacy Policy</div>

</div>
</body>
</html>
```